Pawn & Gun store business card design

Hello! We would like a new business card design for our pawn & gun store. We loan money on items of value and sell firearms, jewelry, electronics & more.

Card will need to have the following information:

Business name - Prairie Nickel Pawn & Gun
Address - 2417 Hwy 53 S. Suite C Bramwell, KS 75246
Employees name - Darren Kellum
Phone number - 972-613-8840
Email - PrairieNickelPawn@Mailvera.com
Website - PrairieNickelPawn.com

Somewhere on the card we would like it to say "Offering 10 Month Layaway!" & "We buy & loan on anything of value!". Our main store color is orange (please see logo). Logo does not have to be on the business card but it can be. Would like the back to have an area to write a note on the back. We like vintage things like old coins, collectables, firearms and more so think about this in the design. We want a business card as unique as our store!

Colors

Designer to choose colors to be used in the design.

Requirements
Nice to have
• Vintage Style

```html
<!DOCTYPE html>
<html lang="en">
<head>
<meta charset="utf-8">
<title>Prairie Nickel Pawn &amp; Gun – Business Card</title>
<link href="https://fonts.googleapis.com/css2?family=Libre+Baskerville:wght@400;700&family=Lato:wght@400&family=Oswald:wght@500&display=swap" rel="stylesheet">
<style>
  :root {
    --brown: #361c0b;
    --orange: #d9581b;
    --white: #ffffff;
    --backdrop: #cfcfcf;
    --divider: #6b4a33;
  }
  * { margin: 0; padding: 0; box-sizing: border-box; }
  html, body { width: 1200px; height: 802px; overflow: hidden; }
  body { background: var(--backdrop); position: relative; font-family: "Lato", sans-serif; }

  .card {
    position: absolute; top: 274px; width: 443px; height: 264px;
    box-shadow: 2px 3px 6px rgba(0,0,0,0.35);
    overflow: hidden;
  }
  .card--front { left: 136px; background: var(--brown); }
  .card--back { left: 624px; background: var(--white); }

  .wordmark {
    position: absolute; top: 62px; left: 0; width: 100%;
    text-align: center; color: var(--white);
    font-family: "Libre Baskerville", serif; font-weight: 700;
    font-size: 34px; line-height: 44px; letter-spacing: 1px; text-transform: uppercase;
    white-space: nowrap;
  }
  .employee-name {
    position: absolute; top: 131px; left: 0; width: 100%;
    text-align: center; color: var(--orange);
    font-family: "Libre Baskerville", serif; font-size: 17px; line-height: 22px;
    text-transform: uppercase; letter-spacing: 0.5px;
  }
  .address {
    position: absolute; top: 171px; right: 239px;
    text-align: right; color: var(--white);
    font-size: 12.5px; line-height: 16px; white-space: nowrap;
  }
  .contact-divider {
    position: absolute; left: 213px; top: 160px; width: 1px; height: 48px;
    background: var(--divider);
  }
  .contact-list {
    position: absolute; left: 222px; top: 160px; list-style: none;
    color: var(--white); font-size: 12.5px; line-height: 16px;
  }
  .contact-list li { display: flex; align-items: center; gap: 5px; white-space: nowrap; }
  .contact-list svg { width: 9px; height: 9px; fill: var(--orange); flex: none; }

  .promo-band {
    position: absolute; left: 0; bottom: 0; width: 100%; height: 42px;
    background: var(--orange); display: flex; justify-content: space-between;
    align-items: center; padding: 0 22px 0 50px;
    font-family: "Oswald", sans-serif; font-weight: 500; font-size: 12px;
    color: var(--brown); text-transform: uppercase; letter-spacing: 0;
  }
  .promo-band span { white-space: nowrap; }

  .back-band {
    position: absolute; top: 0; left: 0; width: 100%; height: 122px;
    background: var(--brown);
  }
  .back-brand {
    position: absolute; top: 70px; left: 0; width: 100%;
    display: flex; justify-content: center; align-items: center; gap: 10px;
  }
  .back-brand__dot { width: 14px; height: 14px; border-radius: 50%; background: var(--orange); }
  .back-brand__name {
    color: var(--orange); font-family: "Libre Baskerville", serif; font-weight: 700;
    font-size: 22px; line-height: 28px; text-transform: uppercase; letter-spacing: 1px;
    white-space: nowrap;
  }
</style>
</head>
<body>

<section class="card card--front" aria-label="Card front">
  <h1 class="wordmark">Prairie Nickel</h1>
  <p class="employee-name">Darren Kellum</p>
  <p class="address">2417 Hwy 53 S<br>Suite C Bramwell, KS 75246</p>
  <div class="contact-divider"></div>
  <ul class="contact-list">
    <li>
      <svg viewBox="0 0 10 10" aria-hidden="true"><path d="M1 3c0-1 1-2 4-2s4 1 4 2v1H7V3H3v1H1zM2 5h6l1 4H1z"/></svg>
      972-613-8840
    </li>
    <li>
      <svg viewBox="0 0 10 10" aria-hidden="true"><path d="M0 2h10v6H0z M0 2l5 3.5L10 2" stroke="#361c0b" stroke-width="0.8"/></svg>
      PrairieNickelPawn@Mailvera.com
    </li>
    <li>
      <svg viewBox="0 0 10 10" aria-hidden="true"><circle cx="5" cy="5" r="4.5"/><path d="M0.5 5h9M5 0.5v9" stroke="#361c0b" stroke-width="0.8"/></svg>
      PrairieNickelPawn.com
    </li>
  </ul>
  <div class="promo-band">
    <span>Offering 10 Month Layaway!</span>
    <span>We Buy &amp; Loan on Anything of Value!</span>
  </div>
</section>

<section class="card card--back" aria-label="Card back with note area">
  <div class="back-band"></div>
  <div class="back-brand">
    <span class="back-brand__dot"></span>
    <span class="back-brand__name">Prairie Nickel Pawn</span>
  </div>
</section>

</body>
</html>
```